Professional BIO Template with photo and logo

Hello,
I need a professional Bio template developed via Microsoft WORD ASAP!!!!! I would like to just be able to add the text I need to add. So resize-able text boxes. Potentially able to adjust the font. These are the things I need added it to include.
Head shot (attached)
Text Box for Name
Text Box for phone number
Text box for email
KVT Logo (attached)
Maybe a blue banner at the top or some background boxes that are blue or grey. Here are the pantone colors that our company uses.

CORE COLOR
100c 91m 17y 6k 38r 58g 128b Hex #263A80 Pantone 7687 C

CORE CONTRAST COLOR
36c 29m 28y 0k 168r 168g 170b Hex #669999 Pantone Cool Gray 6C

I also attached some examples of what we have been looking at. Instead of green add the blue...instead of black maybe just be white.

Thank you

```html
<!DOCTYPE html>
<html lang="en">
<head>
<meta charset="utf-8">
<title>KVT – Team Bio Sheet</title>
<link href="https://fonts.googleapis.com/css2?family=Poppins:wght@400;500;600;700&display=swap" rel="stylesheet">
<style>
  :root {
    --stage: #e8ebee;
    --navy-deep: #16154f;
    --violet: #362a72;
    --violet-footer: #3f3283;
    --white: #ffffff;
    --rule: rgba(255,255,255,0.45);
    --photo-top: #6a6b70;
    --photo-bottom: #2b2c33;
  }
  * { box-sizing: border-box; margin: 0; padding: 0; }
  html, body { width: 976px; height: 1200px; overflow: hidden; }
  body {
    background: var(--stage);
    font-family: "Poppins", sans-serif;
    color: var(--white);
  }
  .bio-sheet {
    position: absolute;
    left: 64px; top: 0;
    width: 848px; height: 1200px;
    background: var(--violet);
    overflow: hidden;
  }
  .header-band {
    position: absolute; left: 0; top: 0;
    width: 848px; height: 306px;
    background: var(--navy-deep);
  }
  .brand {
    position: absolute; left: 652px; top: 76px;
    display: flex; align-items: center; gap: 12px;
  }
  .brand-mark { width: 22px; height: 22px; background: var(--white); }
  .brand-name { font-weight: 600; font-size: 46px; letter-spacing: 2px; line-height: 1; color: var(--white); }

  .headshot { position: absolute; left: 30px; top: 200px; width: 340px; height: 378px; }

  .profile { position: absolute; left: 406px; top: 0; width: 260px; }
  .profile-name {
    position: absolute; top: 325px; left: 0;
    font-weight: 600; font-size: 36px; line-height: 1; white-space: nowrap;
  }
  .profile-rule { position: absolute; left: 0; width: 250px; height: 1px; background: var(--rule); }
  .contact-label { font-weight: 500; font-size: 11.5px; line-height: 1; }
  .contact-value {
    display: flex; align-items: center; gap: 8px;
    font-weight: 500; line-height: 1; white-space: nowrap; margin-top: 7px;
  }
  .contact-value svg { flex: none; }
  .profile .contact { position: absolute; left: 0; }
  .profile .phone { top: 404px; }
  .profile .phone .contact-value { font-size: 17px; }
  .profile .email { top: 472px; }
  .profile .email .contact-value { font-size: 18.5px; }

  .social-links { position: absolute; left: 773px; top: 373px; display: flex; flex-direction: column; gap: 6px; }
  .social-link { width: 38px; height: 38px; border-radius: 50%; background: var(--white); box-shadow: 0 2px 4px rgba(0,0,0,0.3); }

  .about { position: absolute; left: 30px; top: 614px; width: 784px; }
  .about-title { font-weight: 600; font-size: 49px; line-height: 1; margin-left: 5px; letter-spacing: -0.5px; }
  .about-text { font-size: 10.6px; line-height: 25.4px; margin-top: 28px; }
  .about-text + .about-text { margin-top: 19px; }

  .highlights {
    position: absolute; left: 99px; top: 1011px;
    display: grid; grid-template-columns: 380px 380px; row-gap: 12px;
    list-style: none;
  }
  .highlights li { display: flex; align-items: center; gap: 6px; font-size: 12.8px; line-height: 18px; white-space: nowrap; }

  .footer-band {
    position: absolute; left: 0; top: 1136px; width: 848px; height: 64px;
    background: var(--violet-footer);
  }
  .footer-band .contact { position: absolute; top: 12px; }
  .footer-band .phone { left: 228px; }
  .footer-band .email { left: 443px; top: 10px; }
  .footer-band .contact-value { font-size: 17px; margin-top: 6px; }
  .footer-divider { position: absolute; left: 414px; top: 14px; width: 1px; height: 36px; background: var(--rule); }
</style>
</head>
<body>
<main class="bio-sheet">
  <header class="header-band">
    <div class="brand">
      <span class="brand-mark"></span>
      <span class="brand-name">KVT</span>
    </div>
  </header>

  <svg class="headshot" viewBox="0 0 340 378" role="img" aria-label="Head-and-shoulders portrait of Ross Adler in a dark suit and white shirt">
    <defs>
      <linearGradient id="portraitTone" x1="0" y1="0" x2="0" y2="1">
        <stop offset="0" stop-color="var(--photo-top)"/>
        <stop offset="1" stop-color="var(--photo-bottom)"/>
      </linearGradient>
    </defs>
    <path d="M2 2 H338 V208 A168 168 0 0 1 2 208 Z" fill="url(#portraitTone)" stroke="#fff" stroke-width="3"/>
  </svg>

  <section class="profile">
    <h1 class="profile-name">ROSS ADLER</h1>
    <div class="profile-rule" style="top:386px"></div>
    <div class="contact phone">
      <div class="contact-label">Phone Number</div>
      <div class="contact-value">
        <svg width="14" height="14" viewBox="0 0 24 24"><path fill="#fff" d="M6.6 10.8a15.1 15.1 0 0 0 6.6 6.6l2.2-2.2a1 1 0 0 1 1-.25 11.4 11.4 0 0 0 3.6.57 1 1 0 0 1 1 1V20a1 1 0 0 1-1 1A17 17 0 0 1 3 4a1 1 0 0 1 1-1h3.5a1 1 0 0 1 1 1c0 1.25.2 2.45.57 3.57a1 1 0 0 1-.25 1z"/></svg>
        +1 555 014 2290
      </div>
    </div>
    <div class="profile-rule" style="top:457px"></div>
    <div class="contact email">
      <div class="contact-label">Email Address</div>
      <div class="contact-value">
        <svg width="18" height="13" viewBox="0 0 18 13"><rect width="18" height="13" rx="1.5" fill="#fff"/><path d="M1 1.5 9 7.5 17 1.5" fill="none" stroke="#362a72" stroke-width="1.6"/></svg>
        info@rossadler.com
      </div>
    </div>
  </section>

  <nav class="social-links" aria-label="Social profiles">
    <span class="social-link" role="img" aria-label="Social profile link"></span>
    <span class="social-link" role="img" aria-label="Social profile link"></span>
    <span class="social-link" role="img" aria-label="Social profile link"></span>
  </nav>

  <section class="about">
    <h2 class="about-title">ABOUT ME</h2>
    <p class="about-text">Lorem ipsum dolor sit amet, consectetur adipiscing elit, sed do eiusmod tempor incididunt ut labore et dolore magna aliqua. Ut enim ad minim veniam, quis nostrud exercitation ullamco laboris nisi ut aliquip ex ea commodo consequat. Duis aute irure dolor in reprehenderit in voluptate velit esse cillum dolore eu fugiat nulla pariatur. Excepteur sint occaecat cupidatat non proident, sunt in culpa qui officia deserunt mollit anim id est laborum Lorem ipsum dolor sit amet, consectetur adipiscing elit, sed do eiusmod tempor incididunt ut labore et dolore magna aliqua. Ut enim ad minim veniam, quis nostrud exercitation ullamco laboris nisi ut aliquip ex ea commodo consequat. Duis aute irure dolor in reprehenderit in voluptate velit esse cillum dolore eu fugiat nulla pariatur. Excepteur sint occaecat cupidatat non proident, sunt in culpa qui officia deserunt mollit anim id est laborum</p>
    <p class="about-text">Lorem ipsum dolor sit amet, consectetur adipiscing elit, sed do eiusmod tempor incididunt ut labore et dolore magna aliqua. Ut enim ad minim veniam, quis nostrud exercitation ullamco laboris nisi ut aliquip ex ea commodo consequat. Duis aute irure dolor in reprehenderit in voluptate velit esse cillum dolore eu fugiat nulla pariatur. Excepteur sint occaecat cupidatat non proident, sunt in culpa qui officia deserunt mollit anim id est laborum Lorem ipsum dolor sit amet, consectetur adipiscing elit,</p>
  </section>

  <ul class="highlights">
    <li><svg width="12" height="12" viewBox="0 0 12 12"><circle cx="6" cy="6" r="6" fill="#fff"/><path d="M5 3.5 7.5 6 5 8.5" fill="none" stroke="#362a72" stroke-width="1.8"/></svg>Lorem ipsum dolor sit amet, consectetur adipiscing</li>
    <li><svg width="12" height="12" viewBox="0 0 12 12"><circle cx="6" cy="6" r="6" fill="#fff"/><path d="M5 3.5 7.5 6 5 8.5" fill="none" stroke="#362a72" stroke-width="1.8"/></svg>Lorem ipsum dolor sit amet, consectetur adipiscing</li>
    <li><svg width="12" height="12" viewBox="0 0 12 12"><circle cx="6" cy="6" r="6" fill="#fff"/><path d="M5 3.5 7.5 6 5 8.5" fill="none" stroke="#362a72" stroke-width="1.8"/></svg>Lorem ipsum dolor sit amet, consectetur adipiscing</li>
    <li><svg width="12" height="12" viewBox="0 0 12 12"><circle cx="6" cy="6" r="6" fill="#fff"/><path d="M5 3.5 7.5 6 5 8.5" fill="none" stroke="#362a72" stroke-width="1.8"/></svg>Lorem ipsum dolor sit amet, consectetur adipiscing</li>
    <li><svg width="12" height="12" viewBox="0 0 12 12"><circle cx="6" cy="6" r="6" fill="#fff"/><path d="M5 3.5 7.5 6 5 8.5" fill="none" stroke="#362a72" stroke-width="1.8"/></svg>Lorem ipsum dolor sit amet, consectetur adipiscing</li>
    <li><svg width="12" height="12" viewBox="0 0 12 12"><circle cx="6" cy="6" r="6" fill="#fff"/><path d="M5 3.5 7.5 6 5 8.5" fill="none" stroke="#362a72" stroke-width="1.8"/></svg>Lorem ipsum dolor sit amet, consectetur adipiscing</li>
  </ul>

  <footer class="footer-band">
    <div class="contact phone">
      <div class="contact-label">Phone Number</div>
      <div class="contact-value">
        <svg width="14" height="14" viewBox="0 0 24 24"><path fill="#fff" d="M6.6 10.8a15.1 15.1 0 0 0 6.6 6.6l2.2-2.2a1 1 0 0 1 1-.25 11.4 11.4 0 0 0 3.6.57 1 1 0 0 1 1 1V20a1 1 0 0 1-1 1A17 17 0 0 1 3 4a1 1 0 0 1 1-1h3.5a1 1 0 0 1 1 1c0 1.25.2 2.45.57 3.57a1 1 0 0 1-.25 1z"/></svg>
        +1 555 014 2290
      </div>
    </div>
    <div class="footer-divider"></div>
    <div class="contact email">
      <div class="contact-label">Email Address</div>
      <div class="contact-value">
        <svg width="18" height="13" viewBox="0 0 18 13"><rect width="18" height="13" rx="1.5" fill="#fff"/><path d="M1 1.5 9 7.5 17 1.5" fill="none" stroke="#3f3283" stroke-width="1.6"/></svg>
        info@kvtgroup.com
      </div>
    </div>
  </footer>
</main>
</body>
</html>
```